Modern Business Card for Larkwell 2018

Our company assumes the best about people. We are creating an online community of entrepreneurs and business leaders who struggle with marketing their business online.

This business card should POP! We recently got a new logo and are launching a new website next month, so our business cards should make a statement that feels:
-Fresh
-Smart
-Trustworthy
-Fun

Target Market(s)

small business owners, entrepreneurs

Industry/Entity Type

Digital Marketing

Contact Information for Business Card

Dimensions: 3.5" x 2"

Font styles to use
Sans Serif

Colors
f37122
ffffff

Requirements
Must have
• We need a business card with a modern, bold design. We will use one side of the card as a lead-generation offer, so text on one side will need to fit up to 140 characters. The business card should stick to our core colors (orange, black, and white).
Nice to have
• We think a vertical "portrait" design could be interesting.
Should not have
• Should not look like a traditional business card. The round icon should stand out from a distance.

```html
<!DOCTYPE html>
<html lang="en">
<head>
<meta charset="utf-8">
<title>Larkwell Business Card</title>
<link rel="stylesheet" href="https://fonts.googleapis.com/css2?family=Open+Sans:ital,wght@0,400;0,700;0,800;1,700&family=Tinos:wght@700&family=Yellowtail&display=swap">
<style>
  :root {
    --orange: #e8641f;
    --orange-band: #e2601e;
    --white: #ffffff;
    --card-white: #f4f4f4;
    --ink: #1c1c1c;
    --backdrop: #2a2a2a;
    --rule: #3a3a3a;
  }
  * { margin: 0; padding: 0; box-sizing: border-box; }
  html, body {
    width: 1200px; height: 960px; overflow: hidden;
    background: var(--backdrop);
  }
  .canvas { position: relative; width: 1200px; height: 960px; }

  .card { position: absolute; width: 600px; height: 342px; box-shadow: 0 3px 8px rgba(0,0,0,.5); }

  /* Front */
  .card-front { left: 321px; top: 108px; background: var(--card-white); }
  .brand-dot {
    position: absolute; left: 243px; top: 48px;
    width: 100px; height: 100px; border-radius: 50%;
    background: var(--orange);
  }
  .person-name {
    position: absolute; left: 0; right: 0; top: 176px;
    text-align: center; color: var(--orange);
    font: 400 58px/1 "Yellowtail", cursive;
  }
  .person-title {
    position: absolute; left: 0; right: 0; top: 250px;
    text-align: center; color: var(--ink);
    font: 700 19px/1 "Tinos", serif;
  }
  .contact-band {
    position: absolute; left: 0; right: 0; top: 297px; height: 27px;
    background: var(--orange-band); color: var(--white);
    text-align: center; font: 700 15px/27px "Tinos", serif; letter-spacing: 3px;
  }

  /* Back */
  .card-back { left: 320px; top: 493px; background: var(--orange); color: var(--white); font-family: "Open Sans", sans-serif; }
  .brand-block { position: absolute; left: 28px; top: 58px; width: 260px; text-align: center; }
  .brand-block .mark { width: 38px; height: 38px; border-radius: 50%; background: var(--white); margin: 0 auto 10px; }
  .brand-block .wordmark { font-weight: 800; font-size: 38px; line-height: 1; letter-spacing: 1px; }
  .brand-block .tagline { margin-top: 8px; font-weight: 700; font-style: italic; font-size: 11px; letter-spacing: .5px; text-transform: uppercase; }
  .divider { position: absolute; left: 298px; top: 28px; width: 1px; height: 164px; background: rgba(255,255,255,.55); }
  .offer { position: absolute; left: 322px; top: 27px; width: 260px; }
  .offer .headline { font-weight: 800; font-size: 19.5px; line-height: 21px; text-transform: uppercase; }
  .offer .body { margin-top: 8px; font-size: 14px; line-height: 20px; }
  .offer .url { margin-top: 8px; font-weight: 700; font-size: 17px; }
  .notes-box {
    position: absolute; left: 20px; top: 217px; width: 557px; height: 101px;
    background: var(--card-white); border-radius: 18px;
  }
  .notes-box .line { position: absolute; left: 23px; right: 27px; height: 1px; background: var(--rule); }
  .notes-box .line-1 { top: 31px; }
  .notes-box .line-2 { top: 71px; }
</style>
</head>
<body>
<main class="canvas">
  <section class="card card-front">
    <div class="brand-dot"></div>
    <h1 class="person-name">Dana Whitfield</h1>
    <p class="person-title">Story Marketing Coach</p>
    <p class="contact-band">dana@larkwellnow.com</p>
  </section>

  <section class="card card-back">
    <div class="brand-block">
      <div class="mark"></div>
      <div class="wordmark">LARKWELL</div>
      <div class="tagline">Tell stories that inspire action</div>
    </div>
    <div class="divider"></div>
    <div class="offer">
      <p class="headline">Reach more people.<br>Make more money.<br>Create more impact.</p>
      <p class="body">Get your free Larkwell<br>Starter Package and our<br>marketing guide today at</p>
      <p class="url">Larkwellnow.com/start</p>
    </div>
    <div class="notes-box">
      <div class="line line-1"></div>
      <div class="line line-2"></div>
    </div>
  </section>
</main>
</body>
</html>
```